Law Offices business card

Hi there, I'll need business card for the Law Offices of Colin Matheny. The information must convey his strategic approach and quick resolution to complex business litigation needs. Please emphasize Civil Litigation, Corporate Law, Business Governance and Real Estate Law. Colin has over 25 years of experience in these fields.The card should be modern and edgy and the message should be clear. Please consult his current website for ideas.

```html
<!DOCTYPE html>
<html lang="en">
<head>
<meta charset="utf-8">
<title>Law Offices of Colin Matheny – Business Card</title>
<link rel="stylesheet" href="https://fonts.googleapis.com/css2?family=Jost:wght@500&family=Source+Sans+3:wght@400;600&display=swap">
<style>
  :root {
    --backdrop: #161616;
    --card-light: #f3f3f3;
    --brand-orange: #fa5d02;
    --ink-dark: #3a3a3a;
    --ink-body: #1d1d1d;
    --white: #ffffff;
  }
  * { margin: 0; padding: 0; box-sizing: border-box; }
  html, body { width: 1200px; height: 900px; overflow: hidden; }
  body {
    background: var(--backdrop);
    position: relative;
    font-family: "Source Sans 3", "Myriad Pro", sans-serif;
  }
  .card {
    position: absolute;
    top: 184px;
    height: 490px;
    border-radius: 14px;
    text-align: center;
  }
  .card--front { left: 299px; width: 301px; background: var(--card-light); color: var(--ink-body); }
  .card--back  { left: 645px; width: 305px; background: var(--brand-orange); color: var(--white); }

  .brand-mark {
    position: absolute; top: 62px; left: 0; right: 0;
    display: flex; justify-content: center; align-items: center; gap: 8px;
    font-family: "Jost", sans-serif; font-weight: 500;
    font-size: 24px; letter-spacing: 1px; color: var(--brand-orange);
  }
  .brand-mark__square { width: 16px; height: 16px; background: var(--brand-orange); }

  .firm-title {
    font-family: "Jost", sans-serif; font-weight: 500;
    position: absolute; left: 0; right: 0;
  }
  .firm-title__main { display: block; letter-spacing: -0.5px; line-height: 1; }
  .firm-title__sub {
    display: flex; align-items: center; justify-content: center; gap: 10px;
    letter-spacing: 0.8px; line-height: 1;
  }
  .firm-title__sub::before, .firm-title__sub::after {
    content: ""; height: 1px; background: currentColor; opacity: .8;
  }
  .card--front .firm-title { top: 146px; }
  .card--front .firm-title__main { font-size: 27px; color: var(--brand-orange); }
  .card--front .firm-title__sub { font-size: 18px; color: var(--ink-dark); margin-top: 5px; }
  .card--front .firm-title__sub::before, .card--front .firm-title__sub::after { width: 62px; }

  .card--back .firm-title { top: 216px; }
  .card--back .firm-title__main { font-size: 29px; }
  .card--back .firm-title__sub { font-size: 20px; margin-top: 4px; }
  .card--back .firm-title__sub::before, .card--back .firm-title__sub::after { width: 66px; }

  .person { position: absolute; top: 232px; left: 0; right: 0; }
  .person__name { font-size: 18px; font-weight: 600; color: var(--brand-orange); letter-spacing: .4px; }
  .person__role { font-size: 14px; margin-top: 1px; }

  .address { position: absolute; top: 305px; left: 0; right: 0; font-size: 14px; line-height: 18px; font-style: normal; }

  .contact { position: absolute; top: 374px; left: 0; right: 0; list-style: none; font-size: 14px; line-height: 20.5px; }
  .contact li { display: flex; justify-content: center; align-items: center; gap: 4px; }
  .contact svg { width: 10px; height: 10px; fill: var(--brand-orange); }

  .practice-areas { position: absolute; top: 318px; left: 0; right: 0; list-style: none; font-size: 16px; font-weight: 600; line-height: 24px; }
</style>
</head>
<body>

<section class="card card--front" aria-label="Card front">
  <div class="brand-mark"><span class="brand-mark__square"></span>Matheny Law</div>

  <h1 class="firm-title">
    <span class="firm-title__main">Law Offices of Colin</span>
    <span class="firm-title__sub">Matheny</span>
  </h1>

  <div class="person">
    <p class="person__name">COLIN MATHENY</p>
    <p class="person__role">Attorney</p>
  </div>

  <address class="address">118B Harbor Lane<br>Coral Point, Florida 33410</address>

  <ul class="contact">
    <li><svg viewBox="0 0 10 10"><path d="M2 0.5l1.8 2-1 1.2c.6 1.3 1.5 2.2 2.7 2.8l1.2-1 2 1.8-1 1.7C4.5 9 1 5.5 0.5 2z"/></svg>555-204-3178</li>
    <li><svg viewBox="0 0 10 10"><path d="M2.5 0.5h4v2.5h-4z M0.5 3.5h9v6h-9z M2 5h2v1H2z M2 7h2v1H2z M5.5 5h2.5v3H5.5z"/></svg>555-204-3190</li>
    <li><svg viewBox="0 0 10 10"><path d="M0.5 2h9v6.5h-9z M1 2.5l4 3 4-3" stroke="#f3f3f3" stroke-width=".7"/></svg>colin@mathenylaw.com</li>
    <li><svg viewBox="0 0 10 10"><circle cx="5" cy="5" r="4.5"/><path d="M1 5h8M5 .5c-2 2.5-2 6.5 0 9M5 .5c2 2.5 2 6.5 0 9" stroke="#f3f3f3" stroke-width=".6" fill="none"/></svg>www.mathenylaw.com</li>
  </ul>
</section>

<section class="card card--back" aria-label="Card back">
  <h2 class="firm-title">
    <span class="firm-title__main">Law Offices of Colin</span>
    <span class="firm-title__sub">Matheny</span>
  </h2>
  <ul class="practice-areas">
    <li>Business Litigation</li>
    <li>Real Estate</li>
    <li>Tittle and Closing Services</li>
  </ul>
</section>

</body>
</html>
```